To design a brand identity that is simple and creative with 'Corvane' as the brand name, I like modern simple fonts like helvetica neue, I want to print both sides of the card, I am open to dark front and white back, but the design needs to transfer well to letter heads and email signatures, I am looking for sophisticated and elegant, but open minded about clever and off the wall, I do not do 'boring' Corvane Ventures is the mother company for a small group, specialising in Management & consulting, Software development and construction, we have a high level of integrity, we are transparent and accountable for what we do. my images are provided as a guide only, Im not expecting them to be just copied, Im looking for a creator and passionate thinker, who will put life into their work.

Target Market(s)

usually business minded people who are looking for something different in me, such as leadership, confidence and focus with thinking that is per haps a little outside the box..

Industry/Entity Type

Construction

Requirements
Must have
• clean, minmalistic
Nice to have
• custom logo
Should not have
• boring, traditional

```html
<!DOCTYPE html>
<html lang="en">
<head>
<meta charset="utf-8">
<title>Corvane — Business Card</title>
<link href="https://fonts.googleapis.com/css2?family=Lato:ital,wght@0,300;0,400;0,700;1,400&display=swap" rel="stylesheet">
<style>
  :root {
    --backdrop: #ece8e3;
    --card-dark: #1c1c1e;
    --card-dark-edge: #101011;
    --card-light: #ffffff;
    --brand-orange: #ef6a2a;
    --name-yellow: #f5b400;
    --text-light: #f2f2f2;
    --text-muted: #9a9a9a;
    --text-dark: #2b2b2b;
    --divider: #6a6a6a;
    --band-yellow: #f7a81b;
    --band-red: #e8343a;
    --band-magenta: #b02a72;
    --band-purple: #6b3a86;
    --band-teal: #139a8c;
  }
  * { margin: 0; padding: 0; box-sizing: border-box; }
  html, body {
    width: 1200px; height: 720px; overflow: hidden;
    background: var(--backdrop);
    font-family: "Lato", "Helvetica Neue", Arial, sans-serif;
  }
  .stage { position: relative; width: 1200px; height: 720px; }

  .card {
    position: absolute; width: 525px; height: 300px;
    border-radius: 4px;
    box-shadow: 0 10px 28px rgba(0,0,0,.18);
    overflow: hidden;
  }

  /* Front */
  .card--front { left: 50px; top: 110px; }
  .card__texture {
    position: absolute; inset: 0;
    background: radial-gradient(ellipse at 40% 30%, #2a2a2c 0%, var(--card-dark) 55%, var(--card-dark-edge) 100%);
  }
  .brand {
    position: absolute; display: flex; align-items: center; gap: 14px;
  }
  .brand__dot {
    width: 40px; height: 40px; border-radius: 50%;
    background: var(--brand-orange);
  }
  .brand__name {
    font-weight: 300; color: var(--brand-orange); letter-spacing: 2px; line-height: 1;
  }
  .card--front .brand { left: 120px; top: 32px; }
  .card--front .brand__name { font-size: 50px; }
  .tagline {
    position: absolute; left: 235px; top: 92px;
    font-style: italic; font-size: 13px; color: var(--text-muted); letter-spacing: .5px;
  }
  .services {
    position: absolute; left: 0; top: 118px; width: 525px; height: 62px;
  }
  .services__label {
    font-size: 13px; fill: var(--text-light); font-family: "Lato", "Helvetica Neue", Arial, sans-serif;
  }
  .contact {
    position: absolute; left: 0; top: 196px; width: 525px;
    display: flex; align-items: flex-start;
  }
  .contact__person {
    width: 250px; text-align: right; padding-right: 16px;
    color: var(--text-light);
  }
  .contact__name { color: var(--name-yellow); font-weight: 700; font-size: 17px; }
  .contact__title { font-size: 12px; margin-top: 2px; }
  .contact__address { font-size: 12px; margin-top: 4px; }
  .contact__divider { width: 1px; height: 58px; background: var(--divider); }
  .contact__lines {
    padding-left: 14px; color: var(--text-light); font-size: 12px;
    display: flex; flex-direction: column; gap: 9px; padding-top: 2px;
  }
  .contact__line { display: flex; align-items: center; gap: 7px; }
  .contact__icon { width: 12px; height: 12px; flex: none; }

  /* Back */
  .card--back { left: 625px; top: 310px; background: var(--card-light); }
  .card--back .brand { left: 150px; top: 100px; }
  .card--back .brand__dot { width: 46px; height: 46px; }
  .card--back .brand__name { font-size: 56px; }
  .website {
    position: absolute; left: 0; right: 0; top: 200px; text-align: center;
    color: var(--text-dark); font-size: 16px; letter-spacing: 5px;
  }
</style>
</head>
<body>
<main class="stage">

  <section class="card card--front" aria-label="Card front">
    <div class="card__texture" role="img" aria-label="Dark woven carbon texture background"></div>

    <div class="brand">
      <span class="brand__dot"></span>
      <span class="brand__name">corvane</span>
    </div>
    <p class="tagline">...in the creation business.</p>

    <svg class="services" viewBox="0 0 525 62" aria-label="Services">
      <defs>
        <linearGradient id="band-upper" x1="0" x2="1">
          <stop offset="0" stop-color="var(--band-red)"/>
          <stop offset=".45" stop-color="var(--band-magenta)"/>
          <stop offset=".75" stop-color="var(--band-purple)"/>
          <stop offset="1" stop-color="var(--band-teal)"/>
        </linearGradient>
        <linearGradient id="band-lower" x1="0" x2="1">
          <stop offset="0" stop-color="var(--band-yellow)"/>
          <stop offset=".6" stop-color="#f06a22"/>
          <stop offset="1" stop-color="var(--band-red)"/>
        </linearGradient>
      </defs>
      <line x1="0" y1="1" x2="525" y2="1" stroke="#4a4a4a" stroke-width="1"/>
      <polygon points="250,6 525,6 525,28 250,28" fill="url(#band-upper)"/>
      <polygon points="0,34 236,34 250,6 250,28 244,56 0,56" fill="url(#band-lower)"/>
      <line x1="0" y1="61" x2="525" y2="61" stroke="#4a4a4a" stroke-width="1"/>
      <text class="services__label" x="262" y="22">● Software Development  ● Construction</text>
      <text class="services__label" x="10" y="50">● Management &amp; Consulting</text>
    </svg>

    <div class="contact">
      <div class="contact__person">
        <div class="contact__name">Your Name</div>
        <div class="contact__title">Title</div>
        <div class="contact__address">Po Box 512 Perth 6031</div>
      </div>
      <div class="contact__divider"></div>
      <div class="contact__lines">
        <div class="contact__line">
          <svg class="contact__icon" viewBox="0 0 12 12" aria-hidden="true">
            <circle cx="6" cy="6" r="6" fill="var(--name-yellow)"/>
            <path d="M4 3.2c.4-.3.8-.2 1 .2l.5 1c.1.3 0 .5-.2.7l-.3.3c.3.7.8 1.2 1.5 1.5l.3-.3c.2-.2.4-.3.7-.2l1 .5c.4.2.5.6.2 1-.6.8-1.5.9-2.6.2C4.9 7.4 4 6.5 3.4 5.3c-.5-1-.3-1.7.6-2.1z" fill="var(--card-dark)"/>
          </svg>
          <span>+61 0400 555 019</span>
        </div>
        <div class="contact__line">
          <svg class="contact__icon" viewBox="0 0 12 12" aria-hidden="true">
            <circle cx="6" cy="6" r="6" fill="var(--name-yellow)"/>
            <rect x="2.8" y="3.8" width="6.4" height="4.4" rx=".5" fill="var(--card-dark)"/>
            <path d="M3 4l3 2.2L9 4" fill="none" stroke="var(--name-yellow)" stroke-width=".7"/>
          </svg>
          <span>names@corvane.ventures</span>
        </div>
      </div>
    </div>
  </section>

  <section class="card card--back" aria-label="Card back">
    <div class="brand">
      <span class="brand__dot"></span>
      <span class="brand__name">corvane</span>
    </div>
    <p class="website">www.corvane.com</p>
  </section>

</main>
</body>
</html>
```